Website Design for a different kind of Business Consulting organisation needed!

We need a website design that reflects who we are, the simplicity of our consulting business and with a focus on our priority - to help our clients deliver, or execute - the "e" in Dravenholt.

Our key high level requirements are:
1) Simple and intuitive look and feel
2) Integration with all key social media platforms, twitter, facebook, linkedin, tumblr.

10 pages, tops.
- Main page - Welcome
- About Us/ Who are Dravenholt?
- 5 services pages - Project Management, Business Process Management, Change Management, Business Analysis and Finance Systems
- Contact Us

Something like:
http://www.lumvexhold.example/

Dravenholt is a registered trademark and all Logos and other branded material are attached for reference.

So, what’s our gig: A few snippets from previous work...

We are a different kind of business consulting group. We partner with our clients to help them deliver change. We don't just provide them with the theory. We also provide them with the leadership and capability to execute the change.

We aren’t a one stop shop, and we don’t offer cookie cutter solutions. We’re a boutique consulting firm covering Project Management, Business Process Management, Change Management and Business Analytics.

Dravenholt is a professional services organisation that partners with their clients to lead the execution of strategic process and system improvement initiatives. Dravenholt combines hands on delivery with coaching in best practice methodologies and approaches to build their clients capabilities to ensure their ongoing success in project implementations.

UPDATES:

Thanks to everyone who has submitted designs so far. The standard of designs coming through is quite high, with lots of professional designs that nail the design brief. Eliminating them is proving to be quite challenging.

A few updates to the job brief:
- Please make sure the design fits on one page. We would like all of our information to be on the first page that people see without them having to scroll down
- Please ensure you include the FIVE services we offer in the design
- Please use corporate images/istock photos in your designs which are relevant to our business
- Please add a section for a live twitter feed from our twitter account and a link to google+
- Please add a section for news/updates

Also, if you are able to build a site once a design is selected, please let us know.

Thanks,

Maribel.

Target Market(s)

Our target customers are large enterprises in Australia that are growing rapidly and have recently (last 24 months) undertaken or are currently undergoing software implementations and business process improvement programs. These businesses have a turnover of $100m or above and are working hard to differentiate themselves from their competitors but are not seeing the return on investment promised by software vendors and process improvement initiatives.

Industry/Entity Type

Leadership

Requirements
Must have
• Collaboration / Training / Workshop / Consulting images all of a professional nature.
Simple, non-cluttered look with plenty of white space.

```html
<!DOCTYPE html>
<html lang="en">
<head>
<meta charset="utf-8">
<title>Dravenholt | Business Consulting</title>
<link rel="stylesheet" href="https://fonts.googleapis.com/css2?family=Open+Sans:wght@300;400;600;700&display=swap">
<style>
:root{
  --blue:#0057a8;
  --blue-nav:#0066c4;
  --blue-text:#0a5aa8;
  --ink:#333;
  --body:#555;
  --muted:#999;
  --panel:#f0f0f0;
  --page:#fff;
  --top:#f3f3f3;
  --icon:#777;
}
*{box-sizing:border-box;margin:0;padding:0}
html,body{width:963px;height:1200px;overflow:hidden}
body{position:relative;background:var(--page);font-family:'Open Sans',sans-serif;color:var(--body)}
.abs{position:absolute}
.top-band{left:0;top:0;width:963px;height:144px;background:linear-gradient(#fafafa,var(--top))}
.hero-band{left:0;top:144px;width:963px;height:326px;background:var(--blue)}
.brand{font-weight:600;color:var(--blue);letter-spacing:.3px;white-space:nowrap}
.brand-top{left:104px;top:21px;font-size:32px;line-height:40px}
.social{left:746px;top:29px;display:flex;gap:4px}
.social span{width:25px;height:25px;border-radius:50%;background:var(--icon);display:block}
.nav{left:104px;top:75px;width:755px;height:36px;background:var(--blue-nav);border-radius:2px 2px 0 0}
.nav a{position:absolute;top:0;line-height:36px;font-size:11px;font-weight:600;color:#fff;text-decoration:none}
.hero{left:104px;top:111px;width:755px;height:338px;background:#fff;padding:3px}
.hero-photo{width:100%;height:100%;background:linear-gradient(90deg,#3a2c26 0%,#7d6e68 28%,#b9c6d6 45%,#8fa4bd 70%,#4a5566 100%)}
.caption{left:453px;top:233px;width:390px;height:94px;background:rgba(255,255,255,.88);padding:11px 10px 0 13px}
.caption h2{font-size:19.5px;font-weight:700;line-height:27px;color:var(--blue-text);letter-spacing:-.2px}
.dots{display:flex;gap:4px;margin-top:5px}
.dots i{width:11px;height:11px;border-radius:50%;background:#555;display:block}
.dots i:first-child{background:var(--blue-text)}
h3.sec{font-weight:400;font-size:19px;color:var(--ink)}
h3.sec b{font-weight:400;color:var(--blue-text)}
.welcome{left:105px;top:491px;width:498px}
.welcome p{margin-top:6px;width:484px;font-size:10.4px;line-height:20px}
.more{font-weight:300;font-size:20px;color:var(--muted);letter-spacing:.5px}
.welcome .more{margin-top:12px;margin-left:-2px}
.news{left:618px;top:496px;width:241px;height:162px;background:var(--panel);padding:12px 14px 0 14px}
.news h4{margin-top:7px;font-size:12px;font-weight:600;color:var(--blue-text)}
.news p{font-size:10.2px;line-height:16px;margin-top:2px}
.news .date{text-align:right;font-size:10px;font-weight:600;color:var(--blue-text);margin-top:6px}
.news svg{margin-top:5px}
.services{left:104px;top:682px;width:755px;height:285px;background:var(--panel)}
.card{position:absolute;top:16px;width:226px}
.card .photo{width:226px;height:128px}
.card h5{margin-top:8px;font-size:16.5px;font-weight:400;color:var(--blue-text)}
.card p{width:216px;font-size:10.4px;line-height:16px;margin-top:2px}
.card .more{margin-top:9px}
.partners-title{left:105px;top:988px}
.partner-row{left:104px;top:1036px;width:755px;height:24px}
.logo-slot{position:absolute;top:6px;height:12px;background:#9a9a9a;border-radius:2px}
.footer{left:0;top:1101px;width:963px;height:99px;background:var(--blue)}
.brand-foot{left:105px;top:1114px;font-size:23px;line-height:32px;color:#fff}
.foot-nav{right:105px;top:1122px;display:flex;gap:18px}
.foot-nav a{font-size:10px;color:#fff;text-decoration:none}
.copy{left:104px;top:1166px;font-size:10px;color:#e3ecf6;letter-spacing:.3px}
</style>
</head>
<body>
<div class="abs top-band"></div>
<div class="abs hero-band"></div>

<div class="abs brand brand-top">Dravenholt</div>
<div class="abs social" aria-label="Social links"><span></span><span></span><span></span><span></span></div>

<nav class="abs nav">
  <a style="left:24px">Home</a>
  <a style="left:96px">About Us</a>
  <a style="left:189px">Services</a>
  <a style="left:278px">Latest News</a>
  <a style="left:394px">Partners</a>
  <a style="left:489px">Blog</a>
  <a style="left:564px">Contact Us</a>
</nav>

<div class="abs hero">
  <div class="hero-photo" role="img" aria-label="Businesswoman in glasses in front of colleagues in a bright office"></div>
</div>
<div class="abs caption">
  <h2>Nam fermentum vestibulum purus<br>id aliquet</h2>
  <div class="dots"><i></i><i></i><i></i><i></i></div>
</div>

<section class="abs welcome">
  <h3 class="sec">Welcome to <b>Dravenholt</b></h3>
  <p>Aliquam molestie, mi et imperdiet euismod, dui purus auctor tellus, et interdum lacus lectus et ante. Sed accumsan sollicitudin sapien, sit amet adipiscing turpis gravida ac. In congue, neque ac lobortis volutpat, libero mauris varius mi, vitae suscipit ipsum ligula vitae risus. Duis aliquam nibh a dui iaculis viverra id a velit. Vivamus egestas risus in magna varius commodo. Sed semper viverra egestas. Etiam pretium porttitor lectus, vel ornare neque porta volutpat.</p>
  <div class="more">READ MORE</div>
</section>

<aside class="abs news">
  <h3 class="sec">Latest <b>News</b></h3>
  <h4>Sed semper viverra egestas.</h4>
  <p>Etiam pretium porttitor lectus, vel ornare neque porta volutpat. Vivamus egestas risus in magna varius commodo.</p>
  <div class="date">Mar21, 2014</div>
  <svg width="30" height="12" viewBox="0 0 30 12"><path d="M7 1 2 6l5 5M23 1l5 5-5 5" fill="none" stroke="#666" stroke-width="2"/></svg>
</aside>

<section class="abs services">
  <div class="card" style="left:15px">
    <div class="photo" role="img" aria-label="Hand moving a chess piece over a row of pawns" style="background:linear-gradient(135deg,#5a5040,#c8bfa8 50%,#6d6350)"></div>
    <h5>Strategic</h5>
    <p>Aenean a nibh eget turpis vehicula tempus ac sed massa. Vestibulum dolor nulla, ultrices ac tincidunt sed, laoreet non est.</p>
    <div class="more">READ MORE</div>
  </div>
  <div class="card" style="left:263px">
    <div class="photo" role="img" aria-label="Team discussing a plan at a glass board" style="background:linear-gradient(90deg,#dfe6ee,#c9b9a6 60%,#8d7a68)"></div>
    <h5>Methodologies</h5>
    <p>Aenean a nibh eget turpis vehicula tempus ac sed massa. Vestibulum dolor nulla, ultrices ac tincidunt sed, laoreet non est.</p>
    <div class="more">READ MORE</div>
  </div>
  <div class="card" style="left:514px">
    <div class="photo" role="img" aria-label="Colleagues stacking hands together in teamwork" style="background:linear-gradient(135deg,#3f6a9a,#c79a7c 50%,#8aa24a)"></div>
    <h5>Implementations</h5>
    <p>Aenean a nibh eget turpis vehicula tempus ac sed massa. Vestibulum dolor nulla, ultrices ac tincidunt sed, laoreet non est.</p>
    <div class="more">READ MORE</div>
  </div>
</section>

<h3 class="abs sec partners-title">Our <b>Partners</b></h3>
<div class="abs partner-row" aria-label="Partner logos">
  <svg class="abs" style="left:0;top:5px" width="10" height="14" viewBox="0 0 10 14"><path d="M8 1 2 7l6 6" fill="none" stroke="#0a5aa8" stroke-width="2.4"/></svg>
  <span class="logo-slot" style="left:24px;width:104px"></span>
  <span class="logo-slot" style="left:162px;width:100px"></span>
  <span class="logo-slot" style="left:304px;width:114px"></span>
  <span class="logo-slot" style="left:454px;width:48px;top:2px;height:20px"></span>
  <span class="logo-slot" style="left:548px;width:185px;top:8px;height:8px"></span>
  <svg class="abs" style="left:745px;top:5px" width="10" height="14" viewBox="0 0 10 14"><path d="M2 1l6 6-6 6" fill="none" stroke="#0a5aa8" stroke-width="2.4"/></svg>
</div>

<footer class="abs footer"></footer>
<div class="abs brand brand-foot">Dravenholt</div>
<nav class="abs foot-nav">
  <a>Home</a><a>About Us</a><a>Services</a><a>Latest News</a><a>Partners</a><a>Blog</a><a>Contact Us</a>
</nav>
<div class="abs copy">Copyright © 2014. All Right Reserved</div>
</body>
</html>
```